Company or website name
- dalewintham.com
- Links to the website
- Vita Forge
- Describe your company and organization and target audience
- Founded by celebrity personal trainer and media personality Dale Wintham, Vita Forge provides high quality on-site fitness and wellness classes, and personal trainers for businesses and residential gyms throughout New York City. Our target audience are residents of high end buildings in NYC, that expect excellence and luxury
- The design should have the following
- This is a 24"x36" Poster for a complimentary event at a high end building. I would like the poster to look high end, luxury and simple and chique. The words should be clear and easy to read. It would be great to have a final copy that we can send to the printer and one which we can edit for future events Here is the text: The Halcott Spires Gym Complimentary Fitness & Wellness Event Complimentary Yoga, Pilates & Interval Training Bootcamp Classes PLUS: 30 Minute Private Training Sessions *Kids Karate Classes Also Available Saturday May 18th, 25th & June 1st Time: 9:00am - 12:15pm Halcott Spires Gym Schedule: 9:00am - 9:30am Yoga 9:45am - 10:15am Interval Training Bootcamp 11:45am -12:15pm Pilates 9:00am - 12:00pm Private Training Sessions Special Introductory Rate on Future Packages During Promotion www.Vitaforge.tv Info@vitaforge.tv
- Other Facts

```html
<!DOCTYPE html>
<html lang="en">
<head>
<meta charset="utf-8">
<title>The Halcott Spires Gym – Complimentary Fitness &amp; Wellness Event</title>
<link href="https://fonts.googleapis.com/css2?family=Roboto:wght@400;700;900&family=Roboto+Condensed:ital,wght@0,700;1,700&display=swap" rel="stylesheet">
<style>
  :root{
    --page:#ffffff;
    --black:#000000;
    --blue:#0b5aa6;
    --yellow:#f6c714;
    --green:#5b7229;
    --white:#ffffff;
    --photo-a:#2a2420;
    --photo-b:#8a6a52;
  }
  *{margin:0;padding:0;box-sizing:border-box}
  html,body{width:1200px;height:961px;overflow:hidden;background:var(--page)}
  body{position:relative;font-family:"Roboto",Arial,sans-serif;color:var(--white)}
  .poster{position:absolute;left:283px;top:0;width:643px;height:961px;background:var(--page)}
  .edge-top{position:absolute;left:0;top:0;width:100%;height:19px;background:var(--black)}
  .edge-bottom{position:absolute;left:0;bottom:0;width:100%;height:19px;background:var(--black)}
  .header{position:absolute;left:9px;top:38px;width:625px;height:88px;background:var(--blue);text-align:center}
  .header-title{font-weight:900;font-size:35px;letter-spacing:.5px;line-height:44px;padding-top:4px;text-transform:uppercase}
  .header-sub{font-weight:400;font-size:22px;line-height:30px;text-transform:uppercase;letter-spacing:.3px}
  .body-panel{position:absolute;left:0;top:134px;width:100%;height:617px;background:var(--black)}
  .schedule-panel{position:absolute;left:0;top:753px;width:100%;height:189px;background:var(--green)}
  .athlete-photo{position:absolute;left:34px;top:137px;width:212px;height:794px;
    background:linear-gradient(180deg,var(--photo-a) 0%,var(--photo-b) 45%,var(--photo-a) 100%);opacity:.85}
  .contact{position:absolute;left:-100px;top:460px;width:320px;transform:rotate(-90deg);
    font-family:"Roboto Condensed",Arial,sans-serif;font-weight:700;font-size:17px;white-space:nowrap;word-spacing:18px;text-align:center}
  .headline{position:absolute;right:27px;top:156px;text-align:right;color:var(--yellow);
    font-weight:900;font-size:25px;line-height:32px;text-transform:uppercase;letter-spacing:.4px}
  .rule{position:absolute;right:0;height:4px;background:var(--yellow)}
  .rule-1{top:276px;width:403px}
  .rule-2{top:423px;width:324px}
  .rule-3{top:539px;width:296px}
  .bonus{position:absolute;right:27px;top:300px;text-align:right;font-family:"Roboto Condensed",Arial,sans-serif;
    font-style:italic;font-weight:700;font-size:28px;line-height:38px}
  .offer{position:absolute;right:27px;top:437px;text-align:right;font-family:"Roboto Condensed",Arial,sans-serif;
    font-style:italic;font-weight:700;font-size:18px;line-height:32px}
  .brand-name{position:absolute;left:326px;top:580px;width:260px;text-align:center;font-weight:400;font-size:50px;letter-spacing:1px}
  .schedule{position:absolute;right:16px;top:760px;text-align:right;font-family:"Roboto Condensed",Arial,sans-serif;font-weight:700}
  .schedule-date{color:var(--yellow);font-size:20px;line-height:30px}
  .schedule-line{font-size:15.5px;line-height:28px}
  .schedule-line em{font-style:italic}
  .schedule-line .label-lg{font-size:19px}
</style>
</head>
<body>
<main class="poster">
  <div class="edge-top"></div>
  <header class="header">
    <h1 class="header-title">The Halcott Spires Gym</h1>
    <p class="header-sub">Complimentary Fitness &amp; Wellness Event</p>
  </header>
  <section class="body-panel"></section>
  <section class="schedule-panel"></section>
  <div class="athlete-photo" role="img" aria-label="Photo of a female athlete in black sportswear mid-kick, punching toward the viewer"></div>
  <p class="contact">www.Vitaforge.tv Info@vitaforge.tv</p>

  <h2 class="headline">Complimentary Yoga,<br>Pilates &amp; Interval Training<br>Bootcamp Classes</h2>
  <div class="rule rule-1"></div>
  <p class="bonus">PLUS FREE:<br>30 minute private<br>training sessions</p>
  <div class="rule rule-2"></div>
  <p class="offer">Special Introductory Rate<br>on Future Packages<br>During Promotion</p>
  <div class="rule rule-3"></div>
  <p class="brand-name">Vita Forge</p>

  <div class="schedule">
    <p class="schedule-date">SAT MAY 18th, 21st &amp; June 1st</p>
    <p class="schedule-line"><span class="label-lg">Schedule</span> &nbsp;Yoga : <em>9:00am - 9:30am</em></p>
    <p class="schedule-line">Interval Training Boot Camp: <em>9:45am - 10:15am</em></p>
    <p class="schedule-line">Pilates: <em>11:45am-12:15pm</em></p>
    <p class="schedule-line">Complimentary Personal Training Available <em>9:00am-12:00pm</em></p>
    <p class="schedule-line">* Kids Karate Classes Also Available</p>
  </div>
  <div class="edge-bottom"></div>
</main>
</body>
</html>
```